Bork Ventures, Inc. Website redesign

Revamp the website, it is old and outdated. www.borkventuresinc.example

Target Market(s)

Information Technology Consulting and Staffing

Coding

Coded - Design and coding required

Number of Pages Required

5+ page

Colors

Designer to choose colors to be used in the design.

Requirements
Must have
• Outlined text boxes just like from the Tolvane.example site. A clean look

```html
<!DOCTYPE html>
<html lang="en">
<head>
<meta charset="utf-8">
<title>Bork Ventures, Inc. — Mission Integrity Results</title>
<link href="https://fonts.googleapis.com/css2?family=Montserrat:wght@300;400;500;700&family=Saira+Semi+Condensed:wght@500;600&display=swap" rel="stylesheet">
<style>
:root{
  --red:#9b1b30;
  --ink:#1f1f1f;
  --text:#3a3a3a;
  --muted:#555;
  --line:#c9c9c9;
  --soft:#f3f3f3;
  --footer:#3b3b3b;
  --hero-a:#0d1f33;
  --hero-b:#3d6285;
}
*{box-sizing:border-box;margin:0;padding:0}
html,body{width:1200px;height:3373px;overflow:hidden;background:#fff}
body{position:relative;font-family:"Montserrat",sans-serif;color:var(--text)}
.abs{position:absolute}
.head-font{font-family:"Saira Semi Condensed","Arial Narrow",sans-serif;font-weight:600}

/* header */
.site-header{position:absolute;left:0;top:0;width:1200px;height:131px;background:#fff}
.brand{position:absolute;display:flex;align-items:center;gap:10px;font-weight:700;letter-spacing:1px;text-transform:uppercase;white-space:nowrap}
.brand .mark{width:20px;height:20px;background:var(--red)}
.header-brand{left:111px;top:46px;font-size:26px;color:var(--ink)}
.contact-bar{position:absolute;right:113px;top:22px;display:flex;gap:12px;align-items:center;font-size:17px}
.contact-bar .item{display:flex;align-items:center;gap:8px}
.contact-bar .phone{color:var(--red)}
.contact-bar .mail{color:var(--ink)}
.main-nav{position:absolute;right:113px;top:76px;display:flex;gap:38px;font-size:15px;color:var(--ink)}
.main-nav span{padding:6px 15px;border-radius:18px}
.main-nav .active{background:#f7dfe3;margin-right:-22px}

/* hero */
.hero{position:absolute;left:0;top:131px;width:1200px;height:560px;overflow:hidden}
.hero-photo{position:absolute;inset:0;background:linear-gradient(100deg,#2b3d52 0%,var(--hero-b) 38%,var(--hero-a) 70%,#08131f 100%)}
.hero-brand{right:113px;top:118px;font-size:58px;color:#fff}
.hero-brand .mark{width:44px;height:44px;background:#fff}
.hero-title{position:absolute;right:113px;top:220px;font-size:47px;color:#fff;font-weight:500;letter-spacing:.5px;white-space:nowrap}
.btn{position:absolute;display:flex;align-items:center;justify-content:center;border-radius:24px;font-size:16px;font-weight:500}
.btn-hero{left:960px;top:305px;width:126px;height:45px;border:2px solid #fff;color:#fff}

/* section headings */
.section-title{position:absolute;left:0;width:1200px;text-align:center;color:var(--red);font-size:34px}
.rule{position:absolute;left:569px;width:63px;height:3px;background:var(--red)}

.about-copy{position:absolute;left:115px;width:970px;text-align:center;font-size:14px;font-weight:300;line-height:24px;color:var(--text)}
.btn-red{left:477px;top:1048px;width:118px;height:44px;background:var(--red);color:#fff}
.btn-outline{left:605px;top:1048px;width:118px;height:44px;border:2px solid #bbb;color:var(--ink)}

.pillars-row{position:absolute;left:0;top:1176px;width:1200px;height:40px;display:flex;align-items:center;justify-content:center;gap:18px}
.pillars-row svg{flex:none}
.pillars-title{color:var(--red);font-size:29px;white-space:nowrap;line-height:40px}

/* pillars */
.pillar{position:absolute;top:1262px;width:400px;height:301px;border:3px solid var(--line);background:#f7f7f7;padding:50px 34px 0}
.pillar h3{font-size:29px;color:var(--ink);margin-top:14px;line-height:40px}
.pillar p{font-size:14px;font-weight:400;line-height:24px;text-align:justify;margin-top:8px;color:var(--text)}
.pillar.featured{border-color:var(--red);background:linear-gradient(135deg,#e9eef3,#fdfdfe 55%,#e4e8ee);box-shadow:0 0 8px rgba(155,27,48,.35)}
.pillar.featured h3{color:var(--red)}

/* services */
.svc{position:absolute;width:272px}
.svc h4{font-size:20px;font-weight:400;color:var(--ink)}
.svc p{font-size:14px;font-weight:300;line-height:21px;margin-top:10px;color:var(--text)}
.svc.left{left:111px;text-align:right}
.svc.right{left:813px;text-align:justify}
.svc.right h4{text-align:left}

/* news */
.news-band{position:absolute;left:0;top:2207px;width:1200px;height:800px;background:var(--soft)}
.card{position:absolute;top:2396px;width:307px;height:445px;background:#fff;border:2px solid #d5d5d5;text-align:center}
.card .kicker{font-size:13px;font-weight:400;margin-top:12px;color:var(--text)}
.card .headline{font-size:15px;font-weight:500;margin-top:8px;color:var(--ink)}
.card .photo{position:absolute;left:0;top:66px;width:303px;height:198px;clip-path:polygon(0 0,100% 0,100% 100%,50% 90%,0 100%)}
.card .date{position:absolute;left:0;width:303px;top:283px;color:var(--red);font-size:17px;font-weight:500;display:flex;justify-content:center;align-items:center;gap:6px}
.card .blurb{position:absolute;left:12px;width:279px;top:318px;font-size:16px;line-height:26px;color:var(--ink)}
.card .bar{position:absolute;left:101px;top:392px;width:102px;height:4px;background:var(--red)}

/* footer */
.footer-shape{position:absolute;left:0;top:2904px}
.footer-brand{left:0;width:1200px;top:3010px;justify-content:center;font-size:32px;color:#fff}
.footer-brand .mark{background:#fff}
.footer-tag{position:absolute;left:0;width:1200px;top:3068px;text-align:center;color:#fff;font-size:25px;font-variant:small-caps;font-weight:400}
.social{position:absolute;top:3149px;width:40px;height:40px;border:2px solid #fff;border-radius:50%}
.footer-nav{position:absolute;left:0;width:1200px;top:3227px;text-align:center;color:#fff;font-size:16px;font-weight:500;word-spacing:2px}
.footer-nav .sep{margin:0 16px}
.footer-rule{position:absolute;left:111px;top:3291px;width:976px;height:1px;background:#888}
.copyright{position:absolute;left:0;width:1200px;top:3320px;text-align:center;color:#fff;font-size:15px}
</style>
</head>
<body>

<header class="site-header">
  <div class="brand header-brand"><span>Bork Ventures</span><span class="mark"></span></div>
  <div class="contact-bar">
    <div class="item phone">
      <svg width="32" height="32" viewBox="0 0 32 32"><circle cx="16" cy="16" r="14.5" fill="none" stroke="#9b1b30" stroke-width="2"/><path d="M11 9l3 0 1.5 4-2 1.5a9 9 0 0 0 4 4l1.5-2 4 1.5v3a2 2 0 0 1-2 2A13 13 0 0 1 9 11a2 2 0 0 1 2-2z" fill="none" stroke="#9b1b30" stroke-width="1.6"/></svg>
      <span>301-555-0147</span>
    </div>
    <div class="item mail">
      <svg width="32" height="32" viewBox="0 0 32 32"><circle cx="16" cy="16" r="14.5" fill="none" stroke="#1f1f1f" stroke-width="2"/><rect x="9" y="11" width="14" height="10" rx="1" fill="none" stroke="#1f1f1f" stroke-width="1.6"/><path d="M9 12l7 5 7-5" fill="none" stroke="#1f1f1f" stroke-width="1.6"/></svg>
      <span>info@borkventuresinc.example</span>
    </div>
  </div>
  <nav class="main-nav">
    <span class="active">Home</span><span>About Us</span><span>Services</span><span>Strategy</span><span>IT News</span><span>Contact Us</span>
  </nav>
</header>

<section class="hero">
  <div class="hero-photo" role="img" aria-label="Two IT consultants with a laptop in front of a glowing digital interface in a server room"></div>
  <div class="brand abs hero-brand"><span>Bork Ventures</span><span class="mark"></span></div>
  <div class="hero-title head-font">MISSION INTEGRITY RESULTS</div>
  <div class="btn btn-hero">Read More</div>
  <svg class="abs" style="left:0;top:440px" width="1200" height="120" viewBox="0 0 1200 120">
    <polygon points="0,20 600,110 1200,0 1200,120 0,120" fill="#fff"/>
    <polyline points="0,22 600,100 1200,2" fill="none" stroke="#2a2a2a" stroke-width="5"/>
    <polyline points="0,36 600,112 1200,16" fill="none" stroke="#444" stroke-width="2"/>
  </svg>
</section>

<h2 class="section-title head-font" style="top:757px">ABOUT US</h2>
<div class="rule" style="top:814px"></div>
<p class="about-copy" style="top:852px">Bork Ventures, Inc. is an 8(a) innovative and rapidly growing full-service IT consulting firm. We provide our clients with cutting-edge technologies and the know-how to apply them to their individual business models. For over 20 + years, we have been providing reliable IT solutions to businesses in the Washington, DC Metro area and beyond. Our comprehensive services provide clients with unique technology solutions that are customized to meet the specific demands of their business.</p>
<p class="about-copy" style="top:960px">Look to our experts for strategic IT guidance, management and services that allows you to take your mind off technology and concentrate on your core area of business. Bork Ventures, Inc. provides cost-efficient solutions that simply make good sense.</p>
<div class="btn btn-red">Read More</div>
<div class="btn btn-outline">Contact Us</div>

<div class="pillars-row">
  <svg width="26" height="28" viewBox="0 0 26 28"><polygon points="26,0 26,28 0,14" fill="#1f1f1f"/></svg>
  <h2 class="pillars-title head-font">THESE ARE THE FIVE PILLARS OF OUR SUCCESSFUL IT STRATEGY:</h2>
  <svg width="26" height="28" viewBox="0 0 26 28"><polygon points="0,0 0,28 26,14" fill="#bdbdbd"/></svg>
</div>

<div class="pillar" style="left:0">
  <svg width="58" height="58" viewBox="0 0 58 58" fill="none" stroke="#2a2a2a" stroke-width="3"><circle cx="29" cy="20" r="9"/><circle cx="29" cy="20" r="3"/><path d="M29 6v5M29 29v5M15 20h5M38 20h5M19 10l3 3M36 27l3 3M39 10l-3 3M22 27l-3 3"/><path d="M6 30l6 16 10 8M52 30l-6 16-10 8"/></svg>
  <h3 class="head-font">ASSESS</h3>
  <p>Our case-specific technology audit and data gathering provides us with a detailed and comprehensive picture.</p>
</div>
<div class="pillar featured" style="left:400px" role="img" aria-label="Faint background photo of a consultant touching a digital network display">
  <svg width="58" height="58" viewBox="0 0 58 58" fill="none" stroke="#9b1b30" stroke-width="3"><circle cx="18" cy="18" r="7"/><circle cx="38" cy="16" r="7"/><path d="M6 44c0-10 6-15 12-15s12 5 12 15M28 30c2-3 6-5 10-5 7 0 12 6 12 15"/></svg>
  <h3 class="head-font">RECOMMEND</h3>
  <p>Our research and analysis is summarized in a proposal for individually designed solutions that suit your business.</p>
</div>
<div class="pillar" style="left:800px">
  <svg width="58" height="58" viewBox="0 0 58 58" fill="none" stroke="#2a2a2a" stroke-width="3"><path d="M12 6l10 10-4 4L8 10zM20 18l22 22M38 36l8-4 8 8-8 8-8-8z"/><path d="M10 50l14-14"/></svg>
  <h3 class="head-font">IMPLEMENT</h3>
  <p>Bork Ventures, Inc. manages all aspects of the implementation process, including design, procurement, project management.</p>
</div>

<h2 class="section-title head-font" style="top:1632px">OUR SERVICES</h2>
<div class="rule" style="top:1690px"></div>

<div class="svc left" style="top:1792px"><h4>Hardware / Software Sales</h4><p>We have access to multiple distributor partners throughout North America, as well as Elite Partner Status</p></div>
<div class="svc left" style="top:1991px"><h4>Professional Services</h4><p>Our team provides experienced leadership and guidance, utilizing the industry standard methodologies.</p></div>
<div class="svc right" style="top:1792px"><h4>Technology Assessment</h4><p>Experience has shown companies that perform objective, third-party technology assessments.</p></div>
<div class="svc right" style="top:1991px"><h4>Technology Consulting</h4><p>Implementing quality solutions is more than applying technology to problems. You need experts.</p></div>

<svg class="abs" style="left:400px;top:1740px" width="400" height="400" viewBox="0 0 400 400">
  <circle cx="200" cy="200" r="190" fill="none" stroke="#2a2a2a" stroke-width="3"/>
  <circle cx="200" cy="200" r="168" fill="#fff" stroke="#9b1b30" stroke-width="8"/>
  <g fill="#fff" stroke="#1f1f1f" stroke-width="3">
    <circle cx="57" cy="86" r="37"/><circle cx="340" cy="86" r="37"/>
    <circle cx="57" cy="285" r="37"/><circle cx="340" cy="285" r="37"/>
  </g>
  <g fill="none" stroke="#1f1f1f" stroke-width="2.5">
    <path d="M40 102V88M50 102V82M60 102V76M70 102V70M38 84l14-10 8 6 14-12"/>
    <rect x="322" y="78" width="30" height="20"/><path d="M316 102h42"/><circle cx="348" cy="74" r="8" fill="#1f1f1f"/>
    <rect x="36" y="275" width="30" height="20"/><circle cx="51" cy="285" r="5"/><path d="M70 295v-8M75 295v-13"/>
    <circle cx="332" cy="275" r="6"/><circle cx="350" cy="273" r="6"/><path d="M320 300c0-10 6-14 12-14s12 4 12 14M340 286c3-3 6-4 10-4 6 0 10 5 10 14"/>
  </g>
  <text x="200" y="210" text-anchor="middle" font-family="Montserrat, sans-serif" font-weight="700" font-size="28" letter-spacing="1" fill="#1f1f1f">BORK VENTURES</text>
</svg>

<div class="news-band"></div>
<h2 class="section-title head-font" style="top:2275px">LATEST NEWS</h2>
<div class="rule" style="top:2341px"></div>

<div class="card" style="left:111px">
  <div class="kicker">Ipsum Dolor Sit</div><div class="headline">NEMO ENIM VOLUPTATEM</div>
  <div class="photo" style="background:linear-gradient(120deg,#8c8f88,#c9c6bf 50%,#4b5560)" role="img" aria-label="Two colleagues discussing work at a laptop in a bright office"></div>
  <div class="date"><svg width="15" height="15" viewBox="0 0 15 15"><circle cx="7.5" cy="7.5" r="6" fill="none" stroke="#9b1b30" stroke-width="1.5"/><path d="M4.5 7.5l2 2 4-4" fill="none" stroke="#9b1b30" stroke-width="1.5"/></svg>April 1, 2019</div>
  <div class="blurb">Nemo enim ipsam voluptatem quia vo luptas sit aspernatur</div>
  <div class="bar"></div>
</div>
<div class="card" style="left:447px">
  <div class="kicker">Ipsum Dolor Sit</div><div class="headline">NEMO ENIM VOLUPTATEM</div>
  <div class="photo" style="background:linear-gradient(120deg,#6e5a4e,#b9aea4 50%,#3c3f45)" role="img" aria-label="Team of four business people meeting around a table with laptops"></div>
  <div class="date"><svg width="15" height="15" viewBox="0 0 15 15"><circle cx="7.5" cy="7.5" r="6" fill="none" stroke="#9b1b30" stroke-width="1.5"/><path d="M4.5 7.5l2 2 4-4" fill="none" stroke="#9b1b30" stroke-width="1.5"/></svg>April 1, 2019</div>
  <div class="blurb">Nemo enim ipsam voluptatem quia vo luptas sit aspernatur</div>
  <div class="bar"></div>
</div>
<div class="card" style="left:781px">
  <div class="kicker">Ipsum Dolor Sit</div><div class="headline">NEMO ENIM VOLUPTATEM</div>
  <div class="photo" style="background:linear-gradient(120deg,#4a4e55,#a7a29c 55%,#2d3036)" role="img" aria-label="Businesswoman in a dark suit standing in an office"></div>
  <div class="date"><svg width="15" height="15" viewBox="0 0 15 15"><circle cx="7.5" cy="7.5" r="6" fill="none" stroke="#9b1b30" stroke-width="1.5"/><path d="M4.5 7.5l2 2 4-4" fill="none" stroke="#9b1b30" stroke-width="1.5"/></svg>April 1, 2019</div>
  <div class="blurb">Nemo enim ipsam voluptatem quia vo luptas sit aspernatur</div>
  <div class="bar"></div>
</div>

<svg class="footer-shape" width="1200" height="469" viewBox="0 0 1200 469"><polygon points="0,96 600,0 1200,96 1200,469 0,469" fill="#3b3b3b"/></svg>
<div class="brand abs footer-brand"><span>Bork Ventures</span><span class="mark"></span></div>
<div class="footer-tag">Mission Integrity Results</div>
<div class="social" style="left:505px" aria-label="Social profile"></div>
<div class="social" style="left:555px" aria-label="Social profile"></div>
<div class="social" style="left:604px" aria-label="Social profile"></div>
<div class="social" style="left:653px" aria-label="Social profile"></div>
<nav class="footer-nav">HOME<span class="sep">|</span>ABOUT US<span class="sep">|</span>SERVICES<span class="sep">|</span>STRATEGY<span class="sep">|</span>IT NEWS<span class="sep">|</span>CONTACT US</nav>
<div class="footer-rule"></div>
<div class="copyright">Copyrights @ 2019 Bork Ventures. All Rights Reserved.</div>

</body>
</html>
```